Simple and Clean business card design

We would like the design to be simple clean and to incorporate our colors.

We are open to your design and talent, we have the dots in our logo as we think of it as data points and we connect data points for people.

We are open to see the great creative and clean design you bring to the table

Contact Information for Business Card

please include: name, position, email, phone and website

Font styles to use
Sans Serif

Requirements
Must have
• my colors incorporated, simplicity
Nice to have
• lots of white space, simplicity
Should not have
• complexicity/ complex art

```html
<!DOCTYPE html>
<html lang="en">
<head>
<meta charset="UTF-8">
<title>Seedline Business Card</title>
<link rel="stylesheet" href="https://fonts.googleapis.com/css2?family=Oswald:wght@500&family=Work+Sans:wght@400;500&display=swap">
<style>
  :root {
    --page-bg: #1a1a1a;
    --card-bg: #232323;
    --card-bg-light: #2e2e2e;
    --accent-blue: #5b7fc9;
    --logo-grey: #a9a9a9;
    --text-white: #f2f2f2;
  }
  * { margin: 0; padding: 0; box-sizing: border-box; }
  html, body {
    width: 1200px; height: 900px; overflow: hidden;
    background: var(--page-bg);
  }
  .canvas {
    position: relative; width: 1200px; height: 900px;
    display: flex; flex-direction: column; align-items: center;
    justify-content: center; gap: 40px;
  }
  .card {
    position: relative; width: 700px; height: 400px;
    background: linear-gradient(135deg, var(--card-bg) 40%, var(--card-bg-light) 100%);
    border-bottom: 6px solid var(--accent-blue);
    box-shadow: 0 14px 30px rgba(0,0,0,0.5);
  }
  .card-front {
    display: flex; align-items: center; justify-content: center;
  }
  .brand {
    display: flex; align-items: center; gap: 14px;
  }
  .brand-dot {
    width: 22px; height: 22px; border-radius: 50%;
    background: var(--accent-blue);
  }
  .brand-name {
    font-family: "Work Sans", sans-serif; font-weight: 500;
    font-size: 88px; letter-spacing: 1px; color: var(--logo-grey);
    line-height: 1;
  }
  .card-back {
    display: flex; align-items: center; justify-content: center;
  }
  .identity {
    text-align: right; padding-right: 26px;
  }
  .person-name {
    font-family: "Oswald", sans-serif; font-weight: 500;
    font-size: 42px; letter-spacing: 1px; color: var(--accent-blue);
    text-transform: uppercase; line-height: 1.1;
  }
  .person-role {
    font-family: "Work Sans", sans-serif; font-size: 20px;
    color: var(--text-white); letter-spacing: 1px;
  }
  .divider {
    width: 2px; height: 126px; background: var(--accent-blue);
  }
  .contact {
    padding-left: 30px;
    font-family: "Work Sans", sans-serif; font-size: 20px;
    color: var(--text-white); letter-spacing: 0.8px; line-height: 1.3;
    list-style: none;
  }
  .contact li { display: flex; align-items: center; gap: 8px; }
  .contact .address { display: block; margin-bottom: 4px; }
  .contact svg { width: 15px; height: 15px; flex: none; }
</style>
</head>
<body>
<main class="canvas">
  <section class="card card-front">
    <div class="brand">
      <span class="brand-dot"></span>
      <span class="brand-name">Seedline</span>
    </div>
  </section>

  <section class="card card-back">
    <div class="identity">
      <h1 class="person-name">Daniel Brooks</h1>
      <p class="person-role">Founder</p>
    </div>
    <div class="divider"></div>
    <ul class="contact">
      <li class="address">418 Willowbend Lane<br>Carver, TX 78021</li>
      <li>
        <svg viewBox="0 0 16 16" aria-hidden="true"><path d="M4 1.5c.6 0 1 .3 1.2.8l.9 2.2c.2.5 0 1-.4 1.3l-.9.7c.6 1.5 1.7 2.6 3.2 3.2l.7-.9c.3-.4.8-.6 1.3-.4l2.2.9c.5.2.8.6.8 1.2v1.8c0 .8-.7 1.3-1.5 1.2C6.2 13 3 9.8 2.5 4.5 2.4 3.7 3 3 3.8 3z" fill="none" stroke="#5b7fc9" stroke-width="1.3"/></svg>
        0412 558 903
      </li>
      <li>
        <svg viewBox="0 0 16 16" aria-hidden="true"><rect x="1.5" y="3.5" width="13" height="9" fill="none" stroke="#5b7fc9" stroke-width="1.3"/><path d="M1.5 3.5 8 9l6.5-5.5" fill="none" stroke="#5b7fc9" stroke-width="1.3"/></svg>
        info@brightmeridian.com
      </li>
      <li>
        <svg viewBox="0 0 16 16" aria-hidden="true"><circle cx="8" cy="8" r="6.5" fill="none" stroke="#5b7fc9" stroke-width="1.2"/><ellipse cx="8" cy="8" rx="3" ry="6.5" fill="none" stroke="#5b7fc9" stroke-width="1.2"/><path d="M1.5 8h13M2.5 5h11M2.5 11h11" stroke="#5b7fc9" stroke-width="1"/></svg>
        www.brightmeridian.com
      </li>
    </ul>
  </section>
</main>
</body>
</html>
```